BOLD & MINIMALIST DESIGN NEEDED

We want a very bold but minimalistic business card design that is impactful and utilizes both sides of the business card. Our current logo is included for your use.

We want bold fonts and good use of negative space. We don't want the logo to overpower the design.

Target Market(s)

Professionals who are building new commercial buildings.

Industry/Entity Type

Construction

Contact Information for Business Card

Name, Title, email, office phone, cell phone, website

Font styles to use
Serif
Sans Serif

Requirements
Must have
• Bold design!

```html
<!DOCTYPE html>
<html lang="en">
<head>
<meta charset="utf-8">
<title>Ridgeline Build – Business Card</title>
<link href="https://fonts.googleapis.com/css2?family=Arimo:wght@400;700&display=swap" rel="stylesheet">
<style>
  :root {
    --bg: #bdbdbd;
    --white: #ffffff;
    --ink: #1c1c1c;
    --lime: #8cc63f;
    --green: #4e7f1b;
    --green-dark: #2f5410;
    --green-mid: #5b8f22;
  }
  * { margin: 0; padding: 0; box-sizing: border-box; }
  html, body { width: 1200px; height: 802px; overflow: hidden; }
  body {
    background: var(--bg);
    font-family: "Arimo", Arial, sans-serif;
    position: relative;
  }
  .card {
    position: absolute;
    top: 246px;
    width: 540px;
    height: 309px;
    border-radius: 16px;
    overflow: hidden;
    box-shadow: 0 10px 24px rgba(0,0,0,.28);
  }

  /* Front */
  .card-front { left: 30px; background: var(--white); }
  .brand {
    position: absolute;
    left: 34px; top: 40px;
    display: flex; align-items: center; gap: 10px;
  }
  .brand-mark { width: 18px; height: 18px; background: var(--lime); flex: none; }
  .brand-name {
    font-weight: 700; font-size: 28px; color: var(--ink); line-height: 1;
  }
  .website {
    position: absolute; right: 34px; top: 30px;
    display: flex; align-items: center; gap: 8px;
    font-size: 15px; color: var(--ink);
  }
  .icon { width: 14px; height: 14px; flex: none; }
  .person { position: absolute; right: 34px; top: 92px; text-align: right; }
  .person-name { font-weight: 700; font-size: 30px; color: var(--green-mid); line-height: 1.1; }
  .person-title {
    display: inline-block; margin-top: 6px;
    background: var(--lime); color: var(--white);
    font-size: 15px; padding: 4px 12px;
  }
  .contacts {
    position: absolute; left: 34px; top: 160px;
    list-style: none; font-size: 15px; color: var(--ink);
    border-top: 1px solid var(--lime); padding-top: 10px; width: 250px;
  }
  .contacts li { display: flex; align-items: center; gap: 8px; line-height: 1.45; }
  .front-band {
    position: absolute; left: 0; right: 0; bottom: 0; height: 46px;
    background: var(--lime);
    display: flex; align-items: center; justify-content: flex-end;
    padding: 0 30px;
  }
  .front-band::before {
    content: ""; position: absolute; left: 0; right: 0; top: -8px; height: 3px;
    background: var(--lime);
  }
  .address { color: var(--white); font-size: 15px; }

  /* Back */
  .card-back {
    left: 630px;
    background: radial-gradient(circle at 40% 55%, var(--green-mid) 0%, var(--green) 45%, var(--green-dark) 100%);
  }
  .back-brand {
    position: absolute; inset: 0;
    display: flex; align-items: center; justify-content: center; gap: 12px;
  }
  .back-brand .brand-mark { background: var(--white); width: 22px; height: 22px; }
  .back-brand .brand-name { color: var(--white); font-size: 36px; }
</style>
</head>
<body>
  <section class="card card-front">
    <div class="brand">
      <span class="brand-mark"></span>
      <span class="brand-name">RIDGELINE BUILD</span>
    </div>
    <div class="website">
      <svg class="icon" viewBox="0 0 14 14" aria-hidden="true"><circle cx="7" cy="7" r="6" fill="#8cc63f"/><path d="M1 7h12M7 1v12" stroke="#fff" stroke-width="1"/></svg>
      www.ridgelinebuild.com
    </div>
    <div class="person">
      <div class="person-name">Marcus Hale</div>
      <div class="person-title">Founder &amp; CEO</div>
    </div>
    <ul class="contacts">
      <li><svg class="icon" viewBox="0 0 14 14" aria-hidden="true"><path d="M3 1l3 3-2 2c1 2 2 3 4 4l2-2 3 3-2 2C6 13 1 8 1 3z" fill="#5b8f22"/></svg>021-555-014-732</li>
      <li><svg class="icon" viewBox="0 0 14 14" aria-hidden="true"><path d="M3 1l3 3-2 2c1 2 2 3 4 4l2-2 3 3-2 2C6 13 1 8 1 3z" fill="#5b8f22"/></svg>055-210-384-916</li>
      <li><svg class="icon" viewBox="0 0 14 14" aria-hidden="true"><path d="M1 7L13 1 9 13 7 8z" fill="#5b8f22"/></svg>hello@ridgelinebuild.com</li>
    </ul>
    <div class="front-band">
      <span class="address">4417 Harbor Point Blvd 210-B, FL 32411</span>
    </div>
  </section>

  <section class="card card-back">
    <div class="back-brand">
      <span class="brand-mark"></span>
      <span class="brand-name">RIDGELINE BUILD</span>
    </div>
  </section>
</body>
</html>
```